WordPress Design for both website and landing page for an expert

I need a clean and stylish design for my new website. I work as an expert (see attached file WHY HOW WHAT), my product is expert opinion (reports) for company evaluations You can use all of the attached pictures colored or black / white. The person is me, you can add other pictures, if you want. The design should be clean and stylish, so you could use white, black, gray, silver and / or one additional color. I have added an idea about my website, see attached file CONCEPT WEBSITE If you have any more information, please do not hesitate to contact us 'Hesitate to ask me ...

```html
<!DOCTYPE html>
<html lang="de">
<head>
<meta charset="utf-8">
<title>Lukas Brenner – Sachverständiger für Firmenbewertungen</title>
<link href="https://fonts.googleapis.com/css2?family=Montserrat:wght@500;600;700&family=Roboto:wght@400;500;700&display=swap" rel="stylesheet">
<style>
:root{
  --black:#000;
  --ink:#111;
  --white:#fff;
  --grey-bg:#f1f1f1;
  --grey-line:#cfcfcf;
  --silver:#b9bec4;
  --hero-a:#5b6066;
  --hero-b:#c9ccd0;
  --text-grey:#444;
}
*{box-sizing:border-box;margin:0;padding:0}
html,body{width:1200px;height:5028px;overflow:hidden}
body{font-family:"Roboto",Arial,sans-serif;color:var(--ink);background:var(--white)}
h1,h2,h3,.brand,.num{font-family:"Montserrat",Arial,sans-serif}
section,header,footer{position:relative;width:1200px}

/* header + hero */
.site-header{height:140px;background:var(--black);display:flex;align-items:center;justify-content:space-between;padding:0 90px;position:absolute;top:0;left:0;z-index:2}
.brand{color:var(--white);font-weight:600;font-size:26px;letter-spacing:6px;display:flex;align-items:center;gap:14px}
.brand-mark{width:22px;height:22px;border:2px solid var(--silver)}
.main-nav{display:flex;gap:34px}
.main-nav a{color:var(--white);text-decoration:none;font-size:15px;font-weight:500}
.hero{height:720px;background:var(--black)}
.hero-photo{position:absolute;left:0;top:140px;width:1200px;height:580px;background:linear-gradient(100deg,var(--hero-a) 0%,#8d9197 45%,var(--hero-b) 100%)}
.hero-text{position:absolute;left:90px;top:330px;color:var(--white)}
.hero-text h1{font-size:50px;font-weight:700;line-height:1.15}
.hero-text p{margin-top:30px;font-size:17px}

/* uses */
.uses{height:525px;text-align:center}
.section-title{font-size:36px;font-weight:700;padding-top:80px}
.use-list{list-style:none;width:615px;margin:70px auto 0;display:flex;flex-direction:column;gap:27px}
.use-list li{background:var(--black);color:var(--white);height:60px;border-radius:6px;display:flex;align-items:center;padding-left:28px;font-size:17px;font-weight:700}

/* why */
.reasons{height:575px;background:var(--black);color:var(--white);text-align:center}
.reasons .section-title{padding-top:60px}
.reason-row{position:absolute;top:140px;left:0;width:1200px}
.reason{position:absolute;width:300px;text-align:center}
.reason svg{display:block;margin:0 auto}
.num{font-size:64px;font-weight:600;margin-top:22px;line-height:1}
.reason h3{font-size:22px;font-weight:600;margin-top:6px}
.reason p{font-size:14px;line-height:1.55;margin-top:20px;padding:0 30px}
.connector{position:absolute;top:65px;height:3px;background:var(--white);width:155px}

/* promise */
.promise{height:470px;text-align:center}
.promise .brand{color:var(--ink);justify-content:center;padding-top:115px;font-size:30px}
.promise .brand-mark{border-color:var(--silver)}
.promise h2{font-size:27px;font-weight:600;margin-top:55px}
.promise p{font-size:17px;line-height:1.6;width:620px;margin:22px auto 0;color:var(--text-grey)}

/* why how what */
.golden{height:1060px;background:var(--grey-bg)}
.golden svg{position:absolute;left:0;top:0}
.golden-item{position:absolute;left:630px;width:420px;text-align:center}
.golden-item h3{font-size:36px;font-weight:700}
.golden-item p{font-size:17px;line-height:1.5;margin-top:30px;color:var(--ink)}

/* about */
.about{height:720px;background:var(--black)}
.about-title{position:absolute;left:535px;top:70px;color:var(--white);font-size:36px;font-weight:700}
.about-photo{position:absolute;left:90px;top:220px;width:405px;height:320px;background:linear-gradient(90deg,#6b6f74,#d7d9dc);border:8px solid var(--white)}
.about-card{position:absolute;left:535px;top:135px;width:570px;height:490px;background:var(--white);padding:40px 25px;display:grid;grid-template-columns:1fr 170px;gap:40px 30px;font-size:14px;line-height:1.45}
.about-card h4{font-family:"Montserrat",Arial,sans-serif;font-size:15px;font-weight:700;margin-bottom:14px}
.badge{width:135px;height:40px;background:#1d3b7a;border-radius:4px;margin-bottom:14px}
.badge.alt{background:#cfd3d8;height:34px}

/* contact */
.contact{height:560px;text-align:center}
.contact .section-title{padding-top:80px}
.contact-form{position:absolute;left:128px;top:190px;width:940px;display:grid;grid-template-columns:1fr 1fr;gap:18px 24px}
.field{height:38px;border:1px solid var(--grey-line);font:14px "Roboto",Arial,sans-serif;padding:0 12px;text-align:left;display:flex;align-items:center;color:#333}
.field.wide{grid-column:1/3;height:112px;align-items:flex-start;padding-top:10px}
.submit{position:absolute;left:528px;top:440px;width:124px;height:44px;background:var(--black);color:var(--white);font-size:16px;border:0;display:flex;align-items:center;justify-content:center}

/* footer */
.site-footer{height:398px;background:var(--black);color:var(--white)}
.site-footer .brand{position:absolute;left:90px;top:140px;font-size:30px}
.footer-col{position:absolute;top:75px}
.footer-col h3{font-size:27px;font-weight:700;margin-bottom:22px}
.footer-col ul{list-style:none;font-size:15px;line-height:2.25}
.footer-col p{font-size:15px;line-height:1.5;width:215px}
.nl-input{width:210px;height:34px;background:var(--white);color:#666;font-size:13px;display:flex;align-items:center;padding-left:10px;margin-top:18px}
.nl-btn{width:80px;height:32px;background:var(--white);color:var(--ink);font-size:14px;display:flex;align-items:center;justify-content:center;margin-top:14px}
.copyright{position:absolute;bottom:25px;width:100%;text-align:center;font-size:14px}
</style>
</head>
<body>

<header class="site-header">
  <div class="brand"><span class="brand-mark"></span>LUKAS BRENNER</div>
  <nav class="main-nav">
    <a href="#">Home</a><a href="#">What I Do</a><a href="#">Why I Do It &amp; How I Do It</a><a href="#">About Me</a><a href="#">Contact</a>
  </nav>
</header>

<section class="hero">
  <div class="hero-photo" role="img" aria-label="Portrait of the consultant in a dark suit in a bright office corridor"></div>
  <div class="hero-text">
    <h1>Sachverständiger für<br>Firmenbewertungen</h1>
    <p>Sie benötigen ein Gutachten zur Ermittlung des Wertes Ihres Unternehmens</p>
  </div>
</section>

<section class="uses">
  <h2 class="section-title">What do you need or can use a report for</h2>
  <ul class="use-list">
    <li>Buying/selling shares or entire companies</li>
    <li>Inheritance matters</li>
    <li>Questions in gain compensations (in divorce)</li>
  </ul>
</section>

<section class="reasons">
  <h2 class="section-title">Why you should work with me</h2>
  <div class="reason-row">
    <div class="connector" style="left:342px"></div>
    <div class="connector" style="left:702px"></div>
    <div class="reason" style="left:90px">
      <svg width="130" height="130" viewBox="0 0 130 130" fill="none" stroke="#fff" stroke-width="5"><circle cx="65" cy="65" r="55"/><path d="M65 30v35l22 14" stroke-linecap="round"/></svg>
      <div class="num">01</div><h3>Schnell</h3>
      <p>Sie bekommen Ihr Gutachten zeitnah (innerhalb von max. 21 Tagen nach Zugang aller benötigten Unterlagen)</p>
    </div>
    <div class="reason" style="left:450px">
      <svg width="130" height="130" viewBox="0 0 130 130" fill="none" stroke="#fff" stroke-width="5" stroke-linejoin="round"><path d="M65 10l45 16v36c0 30-20 50-45 58C40 112 20 92 20 62V26z"/><path d="M44 64l15 15 28-30" stroke-linecap="round"/></svg>
      <div class="num">02</div><h3>Zertifiziert</h3>
      <p>Sie erhalten ein qualifiziertes und belastbares Gutachten von einem zertifizierten Sachverständigen (höchste Akzeptanz bei allen Parteien)</p>
    </div>
    <div class="reason" style="left:810px">
      <svg width="130" height="130" viewBox="0 0 130 130" fill="none" stroke="#fff" stroke-width="5" stroke-linejoin="round"><path d="M25 10h55l22 22v88H25z"/><path d="M80 10v22h22M38 40h30M38 55h40M38 70h20" stroke-linecap="round"/><circle cx="82" cy="85" r="16"/><path d="M94 97l16 16" stroke-linecap="round"/></svg>
      <div class="num">03</div><h3>Verständlich</h3>
      <p>Ihr Gutachten wird für Sie logisch und nachvollziehbar sein und kein "Fachchinesisch" enthalten</p>
    </div>
  </div>
</section>

<section class="promise">
  <div class="brand"><span class="brand-mark"></span>LUKAS BRENNER</div>
  <h2>Mein Qualitätsversprechen:</h2>
  <p>Sollte der avisierte Termin für die Erstellung des Gutachtens überschritten werden, erhalten Sie das Gutachten absolut kostenfrei!<br>(Ich verzichte auf mein Honorar)</p>
</section>

<section class="golden">
  <svg width="1200" height="1060" viewBox="0 0 1200 1060">
    <line x1="300" y1="335" x2="300" y2="715" stroke="#000" stroke-width="2" stroke-dasharray="6 5"/>
    <g font-family="Montserrat, Arial, sans-serif" font-weight="700" font-size="30" text-anchor="middle">
      <circle cx="300" cy="205" r="122" fill="#000"/><circle cx="300" cy="205" r="100" fill="none" stroke="#fff" stroke-width="3"/><circle cx="300" cy="205" r="70" fill="#fff"/><text x="300" y="216">WHY</text>
      <circle cx="300" cy="522" r="122" fill="#000"/><circle cx="300" cy="522" r="100" fill="none" stroke="#fff" stroke-width="3"/><circle cx="300" cy="522" r="70" fill="#fff"/><text x="300" y="533">HOW</text>
      <circle cx="300" cy="838" r="122" fill="#000"/><circle cx="300" cy="838" r="100" fill="none" stroke="#fff" stroke-width="3"/><circle cx="300" cy="838" r="70" fill="#fff"/><text x="300" y="849">WHAT</text>
    </g>
    <circle cx="300" cy="335" r="7" fill="#000"/><circle cx="300" cy="652" r="7" fill="#000"/>
  </svg>
  <div class="golden-item" style="top:105px"><h3>Why I do, what I do</h3><p>Economy is my passion. Economy is made in numbers. Sometimes it is difficult to find the right numbers.</p></div>
  <div class="golden-item" style="top:420px"><h3>How I do, what I do</h3><p>Jedes Gutachten beginnt mit Verstehen. Also stelle ich Ihnen Fragen und höre sehr genau zu.</p></div>
  <div class="golden-item" style="top:755px"><h3>What I do</h3><p>Conducting business valuations in case of ...<br>Durchführung von Unternehmensbewertungen (Wertermittlung) bei</p></div>
</section>

<section class="about">
  <h2 class="about-title">About Me ( Lukas M. Brenner)</h2>
  <div class="about-photo" role="img" aria-label="Photo of the consultant in a white shirt seated at a desk"></div>
  <div class="about-card">
    <div><h4>Professional Experience</h4>10 years as managing director in the fitness market<br>10 years as CMO / business trainer / CEO in an industrial company (fitness industry)<br>outside lecturer at HWBF<br>expert VALTEC</div>
    <div><h4>Field of Activity</h4>Appraisals Company Valuation<br>Marketing<br>Strategic Corporate Governance<br>Corporate Health Management<br>Change Management</div>
    <div><h4>Educations</h4>Bankkaufmann KWK<br>staatl. Geprüfter Betriebswirt (BA)<br>Dipl.-Kfm. (FH)<br>Business Trainer BTVN<br>Lizenzierter Fitnesstrainer FTVD<br>Sachverständiger für Unternehmensbewertungen</div>
    <div><h4>Partners</h4><div class="badge"></div><div class="badge alt"></div></div>
  </div>
</section>

<section class="contact">
  <h2 class="section-title">Contact Us</h2>
  <div class="contact-form">
    <div class="field">Name</div><div class="field">Email</div>
    <div class="field">Phone Number</div><div class="field"><b>Appointments</b></div>
    <div class="field wide">Messages</div>
  </div>
  <div class="submit">Submit</div>
</section>

<footer class="site-footer">
  <div class="brand"><span class="brand-mark"></span>LUKAS BRENNER</div>
  <div class="footer-col" style="left:486px"><h3>Quick Link</h3>
    <ul><li>Home</li><li>What I Do</li><li>Why I Do It &amp; How I Do It</li><li>About Me</li><li>Contact</li></ul>
  </div>
  <div class="footer-col" style="left:764px"><h3>Newsletter</h3>
    <p>Register your email for news for Lukas Brenner</p>
    <div class="nl-input">Enter the email</div>
    <div class="nl-btn">Submit</div>
  </div>
  <div class="copyright">Copyright © 2018 Lukas Brenner All Rights Reserved.</div>
</footer>

</body>
</html>
```